RW Holloway LLC Business Card - Civil Engineering & Consulting Firm

We need a Business Card that is elegant, and masculine.  It is our Professional Civil Engineering & Consulting Company located in San Antonio TX (Not s construction or builder firm- no gears & no tool images please). We provide civil engineering services including  commercial site plans, grading and drainage plans, utility plans, hydraulics and hydrology, land planning, utility coordination, and other general civil engineering services related to commercial and residential development.
We have 2 existing Logos. We would like to convey reliability, strength, trustworthiness and attention to detail.  Blues and orange tones as per logo We are OK with the use of a darker blue in the mix.  We have 2 logo versions - Full Company Name Logo to go on the back of card, & Small Icon Logo for the front w/ personal Info.

Target Market(s)
Architects, Real Estate Developers, Other Strctural Engineers, Surveyers, General Contractors
Industry/Entity Type
Professional Civil Engineering
Contact Information for Business Card
Name, Position, Address, Cell & Office #, email, and company website
Font styles to use
Other font styles liked:
- Avian
Requirements
Should not have
- No Tools, No Gears, no Cranes, or Construction Equipment.

```html
<!DOCTYPE html>
<html lang="en">
<head>
<meta charset="utf-8">
<title>RW Holloway LLC Business Card</title>
<link href="https://fonts.googleapis.com/css2?family=Montserrat:wght@300;400;600;700&display=swap" rel="stylesheet">
<style>
  :root {
    --backdrop: #3b3b3b;
    --card: #171717;
    --edge: #7fb0e0;
    --blue: #6fa6d8;
    --orange: #e98f2c;
    --white: #f2f2f2;
    --rule: #5a86b4;
  }
  * { box-sizing: border-box; margin: 0; padding: 0; }
  html, body {
    width: 1200px; height: 801px; overflow: hidden;
    background: var(--backdrop);
    font-family: "Montserrat", sans-serif;
  }
  .stage {
    position: relative; width: 1200px; height: 801px;
    display: flex; align-items: center; justify-content: center; gap: 40px;
  }
  .card {
    position: relative; width: 540px; height: 309px;
    background: var(--card);
    border-bottom: 2px solid var(--edge);
    border-left: 2px solid var(--edge);
    box-shadow: 0 18px 40px rgba(0,0,0,.45);
    overflow: hidden;
  }

  /* Shared wordmark */
  .wordmark { display: flex; align-items: center; gap: 10px; }
  .wordmark__square { width: 14px; height: 14px; background: var(--orange); flex: none; }
  .wordmark__name {
    font-weight: 300; color: var(--blue); letter-spacing: .08em; white-space: nowrap;
  }
  .tagline {
    color: var(--orange); font-weight: 400; letter-spacing: .28em; text-transform: uppercase;
  }

  /* Front: personal info */
  .front__brand { position: absolute; left: 28px; top: 112px; }
  .front__brand .wordmark__name { font-size: 24px; }
  .front__brand .tagline { font-size: 8px; margin: 8px 0 0 24px; }

  .front__person { position: absolute; right: 28px; top: 30px; text-align: right; width: 220px; }
  .person__name { color: var(--blue); font-weight: 700; font-size: 17px; letter-spacing: .02em; text-transform: uppercase; }
  .person__title { color: var(--white); font-size: 11px; margin-top: 3px; }
  .person__rule { height: 1px; background: var(--rule); margin: 10px 0 10px; }
  .person__address { color: var(--white); font-size: 11px; line-height: 1.55; }

  .front__contacts { position: absolute; left: 28px; bottom: 22px; width: 240px; }
  .contacts__rule { height: 1px; background: var(--rule); margin-bottom: 10px; }
  .contacts__list { list-style: none; }
  .contacts__item {
    display: flex; align-items: center; gap: 8px;
    color: var(--white); font-size: 11px; line-height: 1.75;
  }
  .contacts__icon { width: 11px; height: 11px; flex: none; }

  /* Back: full name */
  .back__panel {
    position: absolute; left: 0; top: 0; width: 190px; height: 100%;
    background: linear-gradient(160deg, #0d0d0d 0%, #1f1f1f 45%, #6c6c6c 80%, #b8b8b8 100%);
  }
  .back__brand { position: absolute; right: 34px; top: 118px; }
  .back__brand .wordmark__name { font-size: 26px; }
  .back__rule { height: 1px; background: var(--rule); margin: 10px 0 8px 24px; }
  .back__brand .tagline { font-size: 9px; margin-left: 24px; }
</style>
</head>
<body>
<main class="stage">

  <section class="card card--front" aria-label="Card front with personal details">
    <div class="front__brand">
      <div class="wordmark">
        <span class="wordmark__square"></span>
        <span class="wordmark__name">RW HOLLOWAY LLC</span>
      </div>
      <p class="tagline">Consulting Engineers</p>
    </div>

    <div class="front__person">
      <p class="person__name">Daniel Brandt</p>
      <p class="person__title">President</p>
      <div class="person__rule"></div>
      <p class="person__address">18340 Harbor Ridge Drive<br>Lakeview CA 90412</p>
    </div>

    <div class="front__contacts">
      <div class="contacts__rule"></div>
      <ul class="contacts__list">
        <li class="contacts__item">
          <svg class="contacts__icon" viewBox="0 0 12 12"><rect x="3" y="1" width="6" height="10" rx="1" fill="none" stroke="#e98f2c" stroke-width="1.4"/></svg>
          555-310-4827
        </li>
        <li class="contacts__item">
          <svg class="contacts__icon" viewBox="0 0 12 12"><path d="M2 3c0 4 3 7 7 7l1.5-1.8-2.2-1.4-1 1C5.8 7.2 4.8 6.2 4.2 4.7l1-1L3.8 1.5z" fill="#e98f2c"/></svg>
          555-310-4828
        </li>
        <li class="contacts__item">
          <svg class="contacts__icon" viewBox="0 0 12 12"><rect x="1" y="2.5" width="10" height="7" fill="#e98f2c"/><path d="M1 2.5l5 4 5-4" fill="none" stroke="#171717" stroke-width="1"/></svg>
          info@rwholloway-eng.com
        </li>
        <li class="contacts__item">
          <svg class="contacts__icon" viewBox="0 0 12 12"><circle cx="6" cy="6" r="5" fill="#e98f2c"/><path d="M1 6h10M6 1c-2 2.5-2 7.5 0 10M6 1c2 2.5 2 7.5 0 10" fill="none" stroke="#171717" stroke-width=".8"/></svg>
          www.rwholloway-eng.com
        </li>
      </ul>
    </div>
  </section>

  <section class="card card--back" aria-label="Card back with company name">
    <div class="back__panel" role="img" aria-label="Large decorative company emblem in silver gradient"></div>
    <div class="back__brand">
      <div class="wordmark">
        <span class="wordmark__square"></span>
        <span class="wordmark__name">RW HOLLOWAY LLC</span>
      </div>
      <div class="back__rule"></div>
      <p class="tagline">Consulting Engineers</p>
    </div>
  </section>

</main>
</body>
</html>
```